Brightwave Reach - Business Card

We need a business card for a Social Media Marketing company that specializes in online marketing for small businesses in Canada using common Social Media platforms such as Pixlora, Chatterly, Blinkpost & Quibber.

I have uploaded a copy of our logo which I would like utilized in the business card. We would like the business card to be modern yet classy design.

Our website is www.brightwavereach.ca

Industry/Entity Type

Marketing

Contact Information for Business Card

Email: info@brightwavereach.ca
Website: www.brightwavereach.ca
Telephone: 604-555-0193

Colors

Designer to choose colors to be used in the design.

Requirements
Must have
• Social Media icons on reverse
• Please add some designs with color.

```html
<!DOCTYPE html>
<html lang="en">
<head>
<meta charset="utf-8">
<title>Brightwave Reach – Business Card</title>
<link href="https://fonts.googleapis.com/css2?family=Open+Sans:wght@400;600;700&display=swap" rel="stylesheet">
<style>
  :root {
    --stage: #e6e6e6;
    --card: #ffffff;
    --ink: #3a3d40;
    --ink-soft: #7a7d80;
    --rule: #55585b;
    --band: #3b3e41;
    --band-text: #f2f2f2;
    --foliage-a: #ececec;
    --foliage-b: #f7f7f7;
  }
  * { margin: 0; padding: 0; box-sizing: border-box; }
  html, body { width: 1200px; height: 1000px; overflow: hidden; }
  body {
    background: var(--stage);
    font-family: "Open Sans", sans-serif;
    color: var(--ink);
    position: relative;
  }
  .card {
    position: absolute;
    left: 250px;
    width: 700px;
    height: 400px;
    background: var(--card);
    box-shadow: 0 6px 18px rgba(0,0,0,.12);
    overflow: hidden;
  }
  .card--front { top: 60px; }
  .card--back { top: 540px; }

  .foliage {
    position: absolute;
    left: 0; top: 0;
    width: 300px; height: 400px;
    background: radial-gradient(ellipse at 40% 60%, var(--foliage-a) 0%, var(--foliage-b) 55%, var(--card) 80%);
  }
  .brand {
    display: flex;
    align-items: center;
    gap: 10px;
    font-weight: 700;
    color: var(--ink);
    text-transform: uppercase;
    letter-spacing: .5px;
    line-height: 1.05;
  }
  .brand__square {
    width: 18px; height: 18px;
    border: 3px solid var(--ink);
    flex: none;
  }
  .card--front .brand {
    position: absolute;
    left: 50%; top: 150px;
    transform: translateX(-50%);
    font-size: 34px;
  }
  .socials {
    position: absolute;
    left: 50%; top: 325px;
    transform: translateX(-50%);
    display: flex;
    gap: 12px;
    font-size: 11px;
    font-weight: 600;
    color: var(--ink);
  }

  .card--back .brand {
    position: absolute;
    right: 48px; top: 48px;
    font-size: 26px;
  }
  .rule {
    position: absolute;
    height: 1px;
    background: var(--rule);
  }
  .rule--top { left: 340px; right: 40px; top: 140px; }
  .rule--name { left: 330px; right: 40px; top: 262px; }
  .web-band {
    position: absolute;
    right: 0; top: 188px;
    width: 190px; height: 40px;
    background: var(--band);
    color: var(--band-text);
    font-size: 13px;
    display: flex; align-items: center; justify-content: center;
  }
  .person { position: absolute; left: 40px; top: 230px; }
  .person__name { font-size: 28px; font-weight: 700; letter-spacing: .5px; line-height: 1.1; }
  .person__title { font-size: 18px; color: var(--ink-soft); }
  .contact {
    position: absolute; left: 40px; top: 320px;
    list-style: none; font-size: 14px; color: var(--ink);
  }
  .contact li { display: flex; align-items: center; gap: 10px; margin-bottom: 6px; }
  .contact svg { width: 13px; height: 13px; fill: var(--ink); }
</style>
</head>
<body>
  <section class="card card--front" aria-label="Card front">
    <div class="foliage" role="img" aria-label="Faint maple branch with leaves"></div>
    <div class="brand"><span class="brand__square"></span><span>Brightwave<br>Reach</span></div>
    <div class="socials"><span>Chatterly</span><span>Quibber</span><span>Pixlora</span><span>Blinkpost</span></div>
  </section>

  <section class="card card--back" aria-label="Card back">
    <div class="brand"><span class="brand__square"></span><span>Brightwave<br>Reach</span></div>
    <div class="rule rule--top"></div>
    <div class="web-band">www.brightwavereach.ca</div>
    <div class="person">
      <div class="person__name">MARCEL DUNFORD</div>
      <div class="person__title">Precedent</div>
    </div>
    <div class="rule rule--name"></div>
    <ul class="contact">
      <li><svg viewBox="0 0 24 24"><path d="M6.6 10.8a15.1 15.1 0 0 0 6.6 6.6l2.2-2.2c.3-.3.7-.4 1-.2 1.1.4 2.3.6 3.6.6.6 0 1 .4 1 1V20c0 .6-.4 1-1 1A17 17 0 0 1 3 4c0-.6.4-1 1-1h3.5c.6 0 1 .4 1 1 0 1.3.2 2.5.6 3.6.1.3 0 .7-.2 1z"/></svg>604-555-0193</li>
      <li><svg viewBox="0 0 24 24"><path d="M2 5h20v14H2z M2 5l10 8 10-8" fill="none" stroke="#3a3d40" stroke-width="2"/></svg>info@brightwavereach.ca</li>
    </ul>
  </section>
</body>
</html>
```